Cool business cards

Use my existing logo from mark meadow (see images I have uploaded) and design a really cool non-stuffy business card. I am a divorce mediator.

```html
<!DOCTYPE html>
<html lang="en">
<head>
<meta charset="utf-8">
<title>Mark Meadow – Business Cards</title>
<link href="https://fonts.googleapis.com/css2?family=Khand:wght@600&family=Roboto:wght@400;500&display=swap" rel="stylesheet">
<style>
  :root {
    --backdrop: #c9c9c9;
    --teal: #3499a3;
    --green: #3b8762;
    --brand-green: #2e8a63;
    --tag-teal: #2f9fb0;
    --paper: #f4f4f2;
    --ink: #222222;
    --white: #ffffff;
  }
  * { margin: 0; padding: 0; box-sizing: border-box; }
  html, body { width: 1200px; height: 576px; overflow: hidden; }
  body {
    background: var(--backdrop);
    font-family: "Roboto", Arial, sans-serif;
    position: relative;
  }
  .card {
    position: absolute;
    border-radius: 14px;
    overflow: hidden;
  }
  .card-front {
    left: 82px; top: 139px; width: 484px; height: 293px;
    background: linear-gradient(115deg, var(--teal) 0%, #3a9489 45%, var(--green) 100%);
  }
  .card-back {
    left: 602px; top: 138px; width: 481px; height: 291px;
    background: var(--paper);
  }
  .front-brand {
    position: absolute; left: 0; right: 0; top: 110px;
    text-align: center;
    color: var(--white);
    font-size: 38px; font-weight: 400; letter-spacing: 1px;
    line-height: 46px;
  }
  .tagline { position: absolute; white-space: nowrap; }
  .front-tagline {
    left: 0; right: 0; top: 168px; text-align: center;
    color: var(--white); font-size: 14px; letter-spacing: 0.3px;
  }
  .back-brand {
    position: absolute; left: 30px; top: 44px;
    color: var(--brand-green);
    font-size: 23px; font-weight: 400; letter-spacing: 0.5px;
  }
  .back-tagline {
    left: 30px; top: 72px;
    color: var(--tag-teal); font-size: 9px; letter-spacing: 0.2px;
  }
  .person {
    position: absolute; right: 29px; top: 97px; text-align: right;
  }
  .person-name {
    font-family: "Khand", "Arial Narrow", sans-serif;
    font-weight: 600; font-size: 22px; color: var(--brand-green); line-height: 26px;
  }
  .person-role { font-size: 13px; color: var(--ink); line-height: 18px; }
  .divider {
    position: absolute; left: 30px; right: 29px; top: 187px;
    height: 1.5px; background: var(--brand-green);
  }
  .contacts {
    position: absolute; left: 33px; top: 215px; list-style: none;
  }
  .contacts li {
    display: flex; align-items: center; gap: 9px;
    font-size: 13px; color: var(--ink); height: 18px;
  }
  .contacts svg { width: 11px; height: 11px; fill: var(--brand-green); }
  .address {
    position: absolute; right: 33px; top: 233px;
    text-align: right; font-size: 13px; color: var(--ink); line-height: 18px;
    font-style: normal;
  }
</style>
</head>
<body>
  <section class="card card-front" aria-label="Card front">
    <div class="front-brand">Mark Meadow</div>
    <div class="tagline front-tagline">I AM A DIVORCE MEDIATOR</div>
  </section>

  <section class="card card-back" aria-label="Card back">
    <div class="back-brand">Mark Meadow</div>
    <div class="tagline back-tagline">I AM A DIVORCE MEDIATOR</div>

    <div class="person">
      <div class="person-name">Lena Hartwell</div>
      <div class="person-role">Managing Director</div>
    </div>

    <div class="divider"></div>

    <ul class="contacts">
      <li>
        <svg viewBox="0 0 12 12" aria-hidden="true"><path d="M1 4 Q6 0 11 4 L9 5.5 L8 4.5 Q6 3.8 4 4.5 L3 5.5 Z M3 6 H9 L10 11 H2 Z"/></svg>
        555-010-2040
      </li>
      <li>
        <svg viewBox="0 0 12 12" aria-hidden="true"><path d="M0 2.5 H12 V9.5 H0 Z M0.8 3 L6 7 L11.2 3" stroke="var(--paper)" stroke-width="0.8"/></svg>
        lena@markmeadow.com
      </li>
      <li>
        <svg viewBox="0 0 12 12" aria-hidden="true"><circle cx="6" cy="6" r="5.5"/><path d="M0.5 6 H11.5 M6 0.5 V11.5 M6 0.5 Q2.5 6 6 11.5 M6 0.5 Q9.5 6 6 11.5" stroke="var(--paper)" stroke-width="0.7" fill="none"/></svg>
        www.markmeadow.com
      </li>
    </ul>

    <address class="address">87 Willow Lane, Fairview,<br>Brookton, US 204518</address>
  </section>
</body>
</html>
```